Menu Board

Hi Maribel,

I would like you to design for me a menu board for all my products.

The layout I have hand drawn for you so just follow my layout.

Pho
Noodle salads
Rice
StirFry with Thick Rice Noodles
Spring Rolls Ricepaper Rolls

Poster Size: AO Vertical ( 841W x 1189H)

There are more photos of the rice dishes but I thought I can send this through so you can start and I can send you the rest of the photos when I get back from my photographer.

I will have items descriptions to follow also

• Here are the rest of the photos >

```html
<!DOCTYPE html>
<html lang="en">
<head>
<meta charset="utf-8">
<title>Menu Board</title>
<link rel="stylesheet" href="https://fonts.googleapis.com/css2?family=Fredoka:wght@400;500&display=swap">
<style>
  :root {
    --board: #231f20;
    --rule: #4a4441;
    --band: #776b5e;
    --band-edge: #8a7f72;
    --label: #f3eee6;
    --bowl-light: #f4f1ea;
    --broth: #b8895a;
    --herb: #6f8f3a;
    --chili: #c9643a;
    --fried: #c98a3c;
    --paper: #e9e4d4;
  }
  * { box-sizing: border-box; margin: 0; padding: 0; }
  html, body { width: 1000px; height: 1200px; overflow: hidden; }
  body {
    background: var(--board);
    font-family: "Fredoka", "Trebuchet MS", sans-serif;
    color: var(--label);
  }
  .menu-board {
    width: 1000px;
    height: 1200px;
    display: grid;
    grid-template-rows: 290px 220px 225px 200px 265px;
  }
  .menu-row {
    display: grid;
    border-bottom: 2px solid var(--rule);
  }
  .menu-row:last-child { border-bottom: none; }
  .row-pho { grid-template-columns: 1fr 1fr 1fr; }
  .row-four { grid-template-columns: 1fr 1fr 1fr 1fr; }
  .row-rolls { grid-template-columns: 175px 350px 335px 1fr; }

  .menu-item {
    display: flex;
    flex-direction: column;
    border-right: 2px solid var(--rule);
  }
  .menu-item:last-child { border-right: none; }
  .item-photo-area {
    flex: 1;
    display: flex;
    align-items: center;
    justify-content: center;
  }
  .dish-photo {
    border-radius: 50%;
    box-shadow: 0 4px 12px rgba(0,0,0,.55);
  }
  .row-pho .dish-photo { width: 190px; height: 190px; }
  .row-four .dish-photo { width: 128px; height: 128px; }
  .row-rolls .dish-photo { width: 190px; height: 190px; }

  .photo-pho-beef { background: radial-gradient(circle, var(--broth) 0%, #7c6a4c 45%, var(--bowl-light) 62%, #1c1a19 74%); }
  .photo-pho-chicken { background: radial-gradient(circle, #b99a6a 0%, var(--herb) 45%, var(--bowl-light) 62%, #1c1a19 74%); }
  .photo-pho-tofu { background: radial-gradient(circle, var(--chili) 0%, #b7662f 45%, var(--bowl-light) 62%, #1c1a19 74%); }
  .photo-salad { background: radial-gradient(circle, #c9954e 0%, var(--herb) 40%, var(--bowl-light) 64%, #1c1a19 76%); }
  .photo-fried-rice { background: radial-gradient(circle, #e3a27a 0%, #e9c9a8 45%, #f7f4ee 70%); }
  .photo-spring { background: radial-gradient(circle at 40% 55%, var(--fried) 0%, #b06e2a 38%, #f2eee8 62%, #d8d2c8 100%); }
  .photo-ricepaper { background: radial-gradient(circle at 45% 55%, var(--paper) 0%, #c8d7a4 38%, #c99a62 70%, #8c6a43 100%); }

  .item-label {
    background: var(--band);
    border-top: 1px solid var(--band-edge);
    display: flex;
    align-items: center;
    justify-content: center;
    text-align: center;
    white-space: nowrap;
  }
  .row-pho .item-label { height: 62px; font-size: 36px; font-weight: 500; }
  .row-four .item-label { height: 40px; font-size: 19px; font-weight: 400; }
  .row-four .item-label.label-long { font-size: 15px; }
  .row-rolls .item-label { height: 68px; font-size: 31px; font-weight: 500; }
  .empty-cell { border-right: 2px solid var(--rule); }
  .empty-cell:last-child { border-right: none; }
</style>
</head>
<body>
<main class="menu-board">
  <section class="menu-row row-pho">
    <article class="menu-item">
      <div class="item-photo-area"><div class="dish-photo photo-pho-beef" role="img" aria-label="Bowl of beef pho with herbs"></div></div>
      <h2 class="item-label">Beef Pho</h2>
    </article>
    <article class="menu-item">
      <div class="item-photo-area"><div class="dish-photo photo-pho-chicken" role="img" aria-label="Bowl of chicken pho with onion and herbs"></div></div>
      <h2 class="item-label">Chicken Pho</h2>
    </article>
    <article class="menu-item">
      <div class="item-photo-area"><div class="dish-photo photo-pho-tofu" role="img" aria-label="Bowl of tofu pho"></div></div>
      <h2 class="item-label">Tofu Pho</h2>
    </article>
  </section>

  <section class="menu-row row-four">
    <article class="menu-item">
      <div class="item-photo-area"><div class="dish-photo photo-salad" role="img" aria-label="Beef noodle salad"></div></div>
      <h3 class="item-label">Beef Noodle salads</h3>
    </article>
    <article class="menu-item">
      <div class="item-photo-area"><div class="dish-photo photo-salad" role="img" aria-label="Chicken noodle salad"></div></div>
      <h3 class="item-label">Chicken Noodle salads</h3>
    </article>
    <article class="menu-item">
      <div class="item-photo-area"><div class="dish-photo photo-salad" role="img" aria-label="BBQ pork noodle salad"></div></div>
      <h3 class="item-label">BBQ Pork Noodle salads</h3>
    </article>
    <article class="menu-item">
      <div class="item-photo-area"><div class="dish-photo photo-salad" role="img" aria-label="Tofu noodle salad"></div></div>
      <h3 class="item-label">Tofu Noodle salads</h3>
    </article>
  </section>

  <section class="menu-row row-four">
    <article class="menu-item">
      <div class="item-photo-area"></div>
      <h3 class="item-label">Beef Rice</h3>
    </article>
    <article class="menu-item">
      <div class="item-photo-area"></div>
      <h3 class="item-label">Chicken Rice</h3>
    </article>
    <article class="menu-item">
      <div class="item-photo-area"></div>
      <h3 class="item-label">Tofu Rice</h3>
    </article>
    <article class="menu-item">
      <div class="item-photo-area"><div class="dish-photo photo-fried-rice" role="img" aria-label="Plate of fried rice"></div></div>
      <h3 class="item-label">Fried Rice</h3>
    </article>
  </section>

  <section class="menu-row row-four">
    <article class="menu-item">
      <div class="item-photo-area"></div>
      <h3 class="item-label">Beef StirFry Noodles</h3>
    </article>
    <article class="menu-item">
      <div class="item-photo-area"></div>
      <h3 class="item-label">Chicken StirFry Noodles</h3>
    </article>
    <article class="menu-item">
      <div class="item-photo-area"></div>
      <h3 class="item-label">Tofu StirFry Noodles</h3>
    </article>
    <article class="menu-item">
      <div class="item-photo-area"></div>
      <h3 class="item-label label-long">StirFry with Thick Rice Noodles</h3>
    </article>
  </section>

  <section class="menu-row row-rolls">
    <div class="empty-cell"></div>
    <article class="menu-item">
      <div class="item-photo-area"><div class="dish-photo photo-spring" role="img" aria-label="Fried spring rolls with dipping sauce"></div></div>
      <h2 class="item-label">Spring Rolls</h2>
    </article>
    <article class="menu-item">
      <div class="item-photo-area"><div class="dish-photo photo-ricepaper" role="img" aria-label="Fresh ricepaper rolls"></div></div>
      <h2 class="item-label">Ricepaper Rolls</h2>
    </article>
    <div class="empty-cell"></div>
  </section>
</main>
</body>
</html>
```